New National Dermatology Group needs a business card!

We need a business card for our new national company that has 3 brands within the business:
Lumora Clinics Australia, Tessaly Clinics Australia and Corvane Clinics Australia.
We help people access dermatology services close to home throughout Australia.
We need a business card that has:
all 3 logos on it,
Our websites (there are three, listed above)
Our email (there are three, listed above)
The location of our first clinic: 41 Willow Rd Parramatta (this can then be changed for each location as required)

```html
<!DOCTYPE html>
<html lang="en">
<head>
<meta charset="utf-8">
<title>Business Card – Lumora, Tessaly &amp; Corvane Clinics Australia</title>
<link rel="stylesheet" href="https://fonts.googleapis.com/css2?family=Cinzel:wght@600&family=Roboto:ital,wght@0,400;1,400&family=Roboto+Condensed:wght@700&display=swap">
<style>
  :root {
    --bg: #c4c4c4;
    --paper: #ffffff;
    --green: #1fa64a;
    --orange: #f07d1f;
    --brown: #8a3f14;
    --ink: #3a3a3a;
  }
  * { box-sizing: border-box; margin: 0; padding: 0; }
  html, body { width: 1200px; height: 800px; overflow: hidden; }
  body {
    background: var(--bg);
    display: flex;
    align-items: center;
    justify-content: center;
    gap: 80px;
    font-family: "Roboto", Arial, sans-serif;
    color: var(--ink);
  }
  .card {
    width: 380px;
    height: 650px;
    background: var(--paper);
    padding: 16px;
    box-shadow: 0 6px 18px rgba(0,0,0,.18);
  }
  .card__frame {
    width: 100%;
    height: 100%;
    box-shadow:
      inset 0 0 0 2px var(--green),
      inset 0 0 0 4px var(--paper),
      inset 0 0 0 5px var(--orange),
      inset 0 0 0 7px var(--paper),
      inset 0 0 0 8px var(--brown);
    display: flex;
    flex-direction: column;
    align-items: center;
    text-align: center;
    overflow: hidden;
  }

  .divider { width: 22px; height: 2px; flex: none; }
  .divider--ink { background: var(--brown); }
  .divider--green { background: var(--green); }
  .divider--orange { background: var(--orange); }

  /* Front: contact side */
  .card__frame--contact { justify-content: space-evenly; padding: 20px 0; }
  .person__name {
    font-family: "Cinzel", Georgia, serif;
    font-weight: 600;
    font-size: 30px;
    color: var(--green);
    letter-spacing: 1px;
    line-height: 1;
  }
  .person__role {
    font-style: italic;
    font-size: 15px;
    color: var(--orange);
    margin-top: 4px;
  }
  .clinic { display: flex; flex-direction: column; align-items: center; }
  .clinic__icons { display: flex; gap: 4px; margin-bottom: 6px; }
  .clinic__icons svg { width: 19px; height: 19px; display: block; }
  .clinic--lumora .clinic__icons { color: var(--green); }
  .clinic--tessaly .clinic__icons { color: var(--orange); }
  .clinic--corvane .clinic__icons { color: var(--brown); }
  .clinic__details {
    font-style: normal;
    font-size: 14px;
    line-height: 1.3;
    color: var(--ink);
  }

  /* Back: brand side */
  .card__frame--brands { justify-content: center; gap: 30px; }
  .brand { display: flex; flex-direction: column; align-items: center; }
  .brand__name {
    display: flex;
    align-items: center;
    gap: 8px;
    font-family: "Roboto", Arial, sans-serif;
    font-weight: 400;
    font-size: 23px;
    line-height: 1.2;
    white-space: nowrap;
  }
  .brand__mark { width: 14px; height: 14px; border-radius: 50%; background: currentColor; flex: none; }
  .brand--lumora .brand__name { color: var(--green); }
  .brand--tessaly .brand__name { color: var(--orange); }
  .brand--corvane .brand__name { color: var(--brown); }
  .brand__web {
    margin-top: 10px;
    font-family: "Roboto Condensed", Arial, sans-serif;
    font-weight: 700;
    font-size: 17px;
    color: var(--ink);
    letter-spacing: .3px;
  }
</style>
</head>
<body>

<svg width="0" height="0" style="position:absolute" aria-hidden="true">
  <defs>
    <symbol id="icon-pin" viewBox="0 0 20 20">
      <circle cx="10" cy="10" r="10" fill="currentColor"/>
      <path d="M10 4.5a3.5 3.5 0 0 0-3.5 3.5c0 2.6 3.5 7 3.5 7s3.5-4.4 3.5-7A3.5 3.5 0 0 0 10 4.5z" fill="#fff"/>
      <circle cx="10" cy="8" r="1.3" fill="currentColor"/>
    </symbol>
    <symbol id="icon-phone" viewBox="0 0 20 20">
      <circle cx="10" cy="10" r="10" fill="currentColor"/>
      <path d="M7 5.5l1.6 2.3-1 1.1c.6 1.3 1.6 2.3 2.9 2.9l1.1-1 2.3 1.6-.8 1.8c-3.8-.3-6.7-3.2-7-7z" fill="#fff"/>
    </symbol>
    <symbol id="icon-mail" viewBox="0 0 20 20">
      <circle cx="10" cy="10" r="10" fill="currentColor"/>
      <rect x="5" y="6.5" width="10" height="7" rx="1" fill="#fff"/>
      <path d="M5.5 7l4.5 3.5L14.5 7" stroke="currentColor" stroke-width="1" fill="none"/>
    </symbol>
    <symbol id="icon-web" viewBox="0 0 20 20">
      <circle cx="10" cy="10" r="10" fill="currentColor"/>
      <circle cx="10" cy="10" r="5" fill="none" stroke="#fff" stroke-width="1.3"/>
      <path d="M5 10h10M10 5c-2 2.8-2 7.2 0 10M10 5c2 2.8 2 7.2 0 10" fill="none" stroke="#fff" stroke-width="1"/>
    </symbol>
  </defs>
</svg>

<article class="card card--front">
  <div class="card__frame card__frame--contact">
    <header class="person">
      <h1 class="person__name">DANIEL HART</h1>
      <p class="person__role">President</p>
    </header>
    <div class="divider divider--ink"></div>

    <section class="clinic clinic--lumora" aria-label="Lumora Clinics Australia">
      <div class="clinic__icons">
        <svg><use href="#icon-pin"/></svg><svg><use href="#icon-phone"/></svg><svg><use href="#icon-mail"/></svg><svg><use href="#icon-web"/></svg>
      </div>
      <address class="clinic__details">
        41 Willow Rd<br>Parramatta NSW 2150<br>02 5550 1842<br>info@lumoraclinics.com.au<br>lumoraclinics.com.au
      </address>
    </section>

    <section class="clinic clinic--tessaly" aria-label="Tessaly Clinics Australia">
      <div class="clinic__icons">
        <svg><use href="#icon-pin"/></svg><svg><use href="#icon-phone"/></svg><svg><use href="#icon-mail"/></svg><svg><use href="#icon-web"/></svg>
      </div>
      <address class="clinic__details">
        41 Willow Rd<br>Parramatta NSW 2150<br>02 5550 1842<br>info@tessalyclinics.com.au<br>tessalyclinics.com.au
      </address>
    </section>

    <section class="clinic clinic--corvane" aria-label="Corvane Clinics Australia">
      <div class="clinic__icons">
        <svg><use href="#icon-pin"/></svg><svg><use href="#icon-phone"/></svg><svg><use href="#icon-mail"/></svg><svg><use href="#icon-web"/></svg>
      </div>
      <address class="clinic__details">
        41 Willow Rd<br>Parramatta NSW 2150<br>02 5550 1842<br>info@corvaneclinics.com.au<br>corvaneclinics.com.au
      </address>
    </section>
  </div>
</article>

<article class="card card--back">
  <div class="card__frame card__frame--brands">
    <div class="brand brand--lumora">
      <h2 class="brand__name"><span class="brand__mark"></span>Lumora Clinics Australia</h2>
      <p class="brand__web">LUMORACLINICS.COM.AU</p>
    </div>
    <div class="divider divider--green"></div>
    <div class="brand brand--tessaly">
      <h2 class="brand__name"><span class="brand__mark"></span>Tessaly Clinics Australia</h2>
      <p class="brand__web">WWW.TESSALYCLINICS.COM.AU</p>
    </div>
    <div class="divider divider--orange"></div>
    <div class="brand brand--corvane">
      <h2 class="brand__name"><span class="brand__mark"></span>Corvane Clinics Australia</h2>
      <p class="brand__web">WWW.CORVANECLINICS.COM.AU</p>
    </div>
  </div>
</article>

</body>
</html>
```